Coastline Premier Retreats Business Card Design

Design a business card for Coastline Premier Retreats. Look at the website for colors and reference. Card should have logo, name, title, office number, mobile number, email, URL and a tagline like, "Luxury Hotel & Resort Email Marketing" (This might change).

https://www.coastlinepremierretreats.example

The rest I will leave up to your imagination.

Contact Information for Business Card

Logo, name, title, office number, mobile number, email, URL and a tagline like, "Luxury Hotel & Resort Email Marketing" (This might change).

```html
<!DOCTYPE html>
<html lang="en">
<head>
<meta charset="utf-8">
<title>Coastline Premier Retreats – Business Card</title>
<link rel="stylesheet" href="https://fonts.googleapis.com/css2?family=Montserrat:wght@500;700;800&family=Poppins:wght@400;500&display=swap">
<style>
  :root {
    --ink: #0b0b0b;
    --paper: #ffffff;
    --accent: #f47a12;
    --stage: #cfcfcf;
    --muted: #8a8a8a;
  }
  * { box-sizing: border-box; margin: 0; padding: 0; }
  html, body { width: 1200px; height: 800px; overflow: hidden; }
  body {
    background: var(--stage);
    display: flex;
    align-items: center;
    justify-content: center;
    gap: 40px;
    font-family: "Poppins", sans-serif;
  }
  .card {
    position: relative;
    width: 540px;
    height: 310px;
    border-radius: 16px;
    overflow: hidden;
    border-bottom: 3px solid var(--accent);
  }

  /* Front */
  .card--front { background: var(--paper); }
  .front__corner-block {
    position: absolute; top: 0; right: 0;
    width: 58px; height: 78px;
    background: var(--ink);
  }
  .front__person { position: absolute; left: 36px; top: 44px; }
  .person__name {
    font-family: "Montserrat", sans-serif;
    font-weight: 800; font-size: 22px; letter-spacing: 0.5px;
    color: var(--ink); text-transform: uppercase;
  }
  .person__title { font-size: 15px; color: var(--accent); margin-top: 2px; }
  .front__contact-band {
    position: absolute; left: 0; top: 132px;
    width: 322px; height: 96px;
    background: var(--ink);
    padding: 12px 0 0 34px;
    list-style: none;
  }
  .contact__item {
    display: flex; align-items: center; gap: 10px;
    color: var(--paper); font-size: 14px; line-height: 24px;
  }
  .contact__item svg { width: 14px; height: 14px; flex: none; }
  .front__brand {
    position: absolute; right: 40px; top: 150px;
    display: flex; align-items: center; gap: 10px;
  }
  .brand__mark { width: 14px; height: 14px; background: var(--accent); }
  .brand__name {
    font-family: "Montserrat", sans-serif;
    font-weight: 800; font-size: 15px; line-height: 1.15;
    color: var(--ink); text-transform: uppercase;
  }
  .front__url {
    position: absolute; left: 120px; bottom: 30px;
    font-size: 15px; color: var(--ink);
  }

  /* Back */
  .card--back {
    background: var(--ink);
    display: flex; flex-direction: column;
    align-items: center; justify-content: center;
    gap: 34px;
  }
  .back__brand { display: flex; align-items: center; gap: 16px; }
  .back__brand .brand__mark { width: 22px; height: 22px; }
  .back__brand .brand__name { color: var(--paper); font-size: 28px; text-align: left; }
  .back__tagline {
    font-family: "Montserrat", sans-serif;
    font-weight: 800; font-size: 15px; letter-spacing: 1px;
    color: var(--paper); text-transform: uppercase;
  }
</style>
</head>
<body>

  <section class="card card--front" aria-label="Business card front">
    <div class="front__corner-block"></div>

    <div class="front__person">
      <h1 class="person__name">Daniel Hartwell</h1>
      <p class="person__title">Managing Director</p>
    </div>

    <ul class="front__contact-band">
      <li class="contact__item">
        <svg viewBox="0 0 16 16" aria-hidden="true"><path fill="#f47a12" d="M3.5 1.5l2.5 3-1.5 1.5c.8 2 2.5 3.7 4.5 4.5L10.5 9l3 2.5-1.5 3C6.5 14.5 1.5 9.5 1.5 3z"/></svg>
        044-555 010 200
      </li>
      <li class="contact__item">
        <svg viewBox="0 0 16 16" aria-hidden="true"><rect x="4" y="1" width="8" height="14" rx="1.5" fill="none" stroke="#f47a12" stroke-width="1.6"/><circle cx="8" cy="12.3" r="0.9" fill="#f47a12"/></svg>
        044-555 010 201
      </li>
      <li class="contact__item">
        <svg viewBox="0 0 16 16" aria-hidden="true"><rect x="1" y="3" width="14" height="10" fill="#f47a12"/><path d="M1 3l7 6 7-6" fill="none" stroke="#0b0b0b" stroke-width="1.3"/></svg>
        info@coastlinepremier.example
      </li>
    </ul>

    <div class="front__brand">
      <span class="brand__mark"></span>
      <span class="brand__name">Coastline Premier<br>Retreats</span>
    </div>

    <p class="front__url">www.coastlinepremierretreats.example</p>
  </section>

  <section class="card card--back" aria-label="Business card back">
    <div class="back__brand">
      <span class="brand__mark"></span>
      <span class="brand__name">Coastline Premier<br>Retreats</span>
    </div>
    <p class="back__tagline">Luxury Hotel &amp; Resort Email Marketing</p>
  </section>

</body>
</html>
```